Marwick Law Letterhead

We need a new letterhead design for a Law Firm. The address for the law firm is 1475 Calloway Street, Suite 210, Houston, Texas 77041. Phone Number: 832-361-9027; Fax Number: 832-614-7359. The logo is uploaded to the project.

```html
<!DOCTYPE html>
<html lang="en">
<head>
<meta charset="utf-8">
<title>Marwick Law Letterhead</title>
<link href="https://fonts.googleapis.com/css2?family=Montserrat:wght@400;500&display=swap" rel="stylesheet">
<style>
  :root {
    --navy: #152a4e;
    --red: #d2151f;
    --red-dark: #7a0710;
    --ink: #2b2b2b;
    --backdrop: #e8e8e8;
    --paper: #ffffff;
  }
  * { margin: 0; padding: 0; box-sizing: border-box; }
  html, body {
    width: 1154px; height: 1200px; overflow: hidden;
    background: var(--backdrop);
    font-family: "Montserrat", Arial, sans-serif;
    color: var(--ink);
  }
  .letterhead {
    position: absolute; left: 152px; top: 6px;
    width: 850px; height: 1188px;
    background: var(--paper);
    box-shadow: 0 6px 24px rgba(0,0,0,0.18);
    overflow: hidden;
  }
  .header-wave { position: absolute; left: 0; top: 0; width: 850px; height: 239px; display: block; }
  .brand {
    position: absolute; left: 300px; top: 156px;
    display: flex; align-items: center; gap: 14px;
  }
  .brand-mark { width: 38px; height: 38px; background: var(--navy); }
  .brand-name { font-size: 34px; font-weight: 500; color: var(--navy); letter-spacing: 0.5px; }
  .recipient {
    position: absolute; left: 32px; top: 284px;
    font-size: 13.5px; line-height: 21px; color: #1e1e1e;
  }
  .letter-body {
    position: absolute; left: 34px; top: 374px; width: 786px;
    font-size: 13.5px; line-height: 21.1px; text-align: justify;
  }
  .letter-body p { margin-bottom: 21.1px; }
  .closing { position: absolute; left: 32px; top: 968px; font-size: 16px; color: #1e1e1e; }
  .signature {
    position: absolute; left: 30px; top: 998px; width: 95px; height: 28px;
    background: linear-gradient(90deg, #d9d9d9, #cfcfcf); border-radius: 3px;
  }
  .contact-bar { position: absolute; left: 0; top: 1096px; width: 850px; height: 64px; }
  .contact-item { position: absolute; display: flex; align-items: center; }
  .contact-item svg { display: block; }
  .contact-number { font-size: 27px; color: #111; margin-left: 14px; }
  .phone { left: 32px; top: 12px; }
  .fax { left: 275px; top: 12px; }
  .location { left: 518px; top: 8px; }
  .address {
    position: absolute; left: 582px; top: 0;
    font-size: 17.5px; line-height: 23px; color: #111;
  }
</style>
</head>
<body>
<main class="letterhead">
  <svg class="header-wave" viewBox="0 0 1066 300" preserveAspectRatio="none" aria-hidden="true">
    <defs>
      <linearGradient id="swoosh" x1="0" x2="1" y1="0" y2="0">
        <stop offset="0" stop-color="#e31c23"/>
        <stop offset="0.6" stop-color="#b80f19"/>
        <stop offset="1" stop-color="#7a0710"/>
      </linearGradient>
    </defs>
    <path d="M0 0 H1066 V80 C760 50 360 80 0 281 Z" fill="var(--navy)"/>
    <path d="M40 268 C320 110 720 55 1066 92 V114 C720 78 340 120 40 268 Z" fill="url(#swoosh)"/>
  </svg>

  <div class="brand">
    <span class="brand-mark"></span>
    <span class="brand-name">Marwick Law</span>
  </div>

  <address class="recipient" style="font-style:normal">
    Mr/s<br>First Name and Last Name<br>Company Name<br>Address
  </address>

  <section class="letter-body">
    <p>Lorem ipsum dolor sit amet,consectetur adipiscing sed do eiusmod tempor incididunt laboreet dolore magna aliqua.Ut enim ad minim.veniam, quis nostrud exercitation ullamco laboris nisi ut aliquip exea commodo consequat.Lorem ipsum dolor sit amet,consectetur adipiscing sed do eiusmod tempor incididunt.labore et dolore magna aliqua. Ut enim</p>
    <p>Lorem ipsum dolor sit amet, consectetur adipiscing sed do eiusmod tempor incididunt labore et dolore magna aliqua. Ut enim ad minim veniam, quis nostrud exercitation ullamco laboris nisi ut aliquip exea commodo consequat.Duis aute irure dolor in reprehenderit in voluptate velit esse cillum irure dolor in reprehenderit in voluptate velit esse irure</p>
    <p>Lorem ipsum dolor sit amet, consectetur adipiscing sed do eiusmod tempor incididunt labore et dolore magna aliqua. consequat. Duis aute irure dolor in.reprehenderit in voluptate velit esse cillum dolore eu fugiat nulla pariatur. Excepteur sint occaecat cupidatat non proident, sunt in culpa qui officia deserunt mollit,</p>
    <p>Lorem ipsum dolor sit amet, consectetur adipiscing sed do eiusmod tempor incididunt labore et dolore magna aliqua. Ut enim Lorem ipsum dolor sit amet, consectetur adipiscing sed do eiusmod tempor incididunt labore et dolore magna aliqua. Ut enim Lorem ipsum aliqua.ipsum</p>
    <p>Lorem ipsum dolor sit amet, consectetur adipiscing sed do eiusmod tempor incididunt labore et dolore magna aliqua. Ut enim ad minim veniam, quis nostrud exercitation ullamco laboris nisi ut aliquip exea commodo consequat.Duis aute irure dolor in reprehenderit in voluptate velit esse cillum irure dolor in reprehenderit in voluptate velit esse irure</p>
    <p>Lorem ipsum dolor sit amet, consectetur adipiscing sed do eiusmod tempor incididunt labore et dolore magna aliqua. Ut enim ad minim veniam, quis nostrud exercitation ullamco laboris nisi ut aliquip exea commodo consequat.Duis aute irure dolor in reprehenderit in voluptate velit esse cillum irure dolor in reprehenderit in voluptate velit esse irure</p>
  </section>

  <p class="closing">Regards</p>
  <div class="signature" role="img" aria-label="Handwritten signature of Ellery"></div>

  <footer class="contact-bar">
    <div class="contact-item phone">
      <svg width="41" height="36" viewBox="0 0 41 36" aria-hidden="true">
        <path d="M4 3 L11 1 L15 10 L11 13 C13 19 18 24 24 27 L27 23 L36 27 L34 34 C20 35 3 20 4 3 Z" fill="var(--red)"/>
        <path d="M21 4 A12 12 0 0 1 33 16" stroke="var(--red)" stroke-width="3" fill="none"/>
        <path d="M21 10 A6 6 0 0 1 27 16" stroke="var(--red)" stroke-width="3" fill="none"/>
      </svg>
      <span class="contact-number">832-361-9027</span>
    </div>
    <div class="contact-item fax">
      <svg width="36" height="38" viewBox="0 0 36 38" aria-hidden="true">
        <rect x="9" y="1" width="18" height="10" rx="1" fill="var(--red-dark)"/>
        <rect x="1" y="10" width="34" height="16" rx="4" fill="var(--red)"/>
        <rect x="8" y="20" width="20" height="17" fill="#fff" stroke="var(--red)" stroke-width="2.5"/>
        <path d="M12 26 H24 M12 31 H24" stroke="var(--red)" stroke-width="2"/>
      </svg>
      <span class="contact-number">832-614-7359</span>
    </div>
    <div class="contact-item location">
      <svg width="32" height="44" viewBox="0 0 32 44" aria-hidden="true">
        <path d="M16 1 C7 1 1 8 1 16 C1 26 16 43 16 43 C16 43 31 26 31 16 C31 8 25 1 16 1 Z" fill="var(--red)"/>
        <circle cx="16" cy="15" r="6" fill="#fff"/>
      </svg>
    </div>
    <address class="address" style="font-style:normal">
      1475 Calloway Street,<br>Suite 210, Houston,<br>Texas 77041
    </address>
  </footer>
</main>
</body>
</html>
```